Logo and Card design for KRV Home Solutions LLC

I need an edgier logo and business card designs. Current logo attached. I like the colors below. I would like the logo to incorporate a home in the design.
Title = Principal-Acquisitions
Email:KRVHOMESOLUTIONS@fernmail.example
555-214-0937
facebook
IG
2 sided business card with the front being contact info a slogan about selling a home fast. The back incorporating What we do. Buy houses, land, or commercial property as is. We find solutions to make the process of selling simple and fair.

Target Market(s)

Motivated house sellers.

Industry/Entity Type

Business

Contact Information for Business Card

Who we are: We are a Faith based Real Estate Investment Company. We pay cash for homes in any condition and can close quick. Whatever the reason you need to sell fast, we can help. We believe in creating win-win solutions to help you in your time of need. We care! We can help!

Logo Text

KRV Home Solutions LLC

Font styles to use
Sans Serif

Colors
33a6d7
0355a3
85abd2
cee9f5
9d9d9d
b2b2b2
ffffff

Requirements
Must have
• Old logo attached. I want something edgier.
• Company name, phone number, description on the back of what we can do. Pay all cash. Buy in as is condition. No fees,Commisions or closing costs.Close quick. No hassles with solutions to meet your unique situation.
• Call today for an offer within 24 hours.

```html
<!DOCTYPE html>
<html lang="en">
<head>
<meta charset="utf-8">
<title>KRV Home Solutions – Business Card</title>
<link rel="stylesheet" href="https://fonts.googleapis.com/css2?family=Roboto:wght@400;500;700&family=Roboto+Condensed:wght@400;700&display=swap">
<style>
  :root {
    --backdrop: #e6e2dc;
    --navy: #1e3567;
    --ink-blue: #233a72;
    --text-grey: #5a5a5a;
    --body-ink: #3f3f3f;
    --divider: #9d9d9d;
    --white: #ffffff;
  }
  * { margin: 0; padding: 0; box-sizing: border-box; }
  html, body { width: 1200px; height: 960px; overflow: hidden; }
  body { background: var(--backdrop); position: relative; font-family: "Roboto", Arial, sans-serif; }

  .card { position: absolute; width: 600px; height: 343px; box-shadow: 0 3px 8px rgba(0,0,0,.25); overflow: hidden; }
  .card--front { left: 314px; top: 113px; }
  .card--back { left: 312px; top: 472px; background: var(--navy); color: var(--white); text-align: center; }

  .front-photo {
    position: absolute; inset: 0;
    background: linear-gradient(180deg, #f1f3f2 0%, #e9ebe6 35%, #e3e5dc 55%, #d6e2c2 75%, #cfdcb8 100%);
  }

  .brand-name {
    position: absolute; left: 0; width: 271px; top: 132px;
    display: flex; justify-content: center; align-items: center; gap: 8px;
    font-family: "Roboto", Arial, sans-serif; font-weight: 500; font-size: 17px;
    color: var(--ink-blue); white-space: nowrap;
  }
  .brand-name__square { width: 10px; height: 10px; background: var(--ink-blue); flex: none; }

  .front-divider { position: absolute; left: 271px; top: 86px; width: 1px; height: 118px; background: var(--divider); }

  .contact-block { position: absolute; left: 293px; top: 88px; font-family: "Roboto Condensed", Arial, sans-serif; }
  .contact-block__name { font-weight: 700; font-size: 23px; color: var(--ink-blue); letter-spacing: .2px; line-height: 1.1; }
  .contact-block__title { font-size: 16px; color: var(--text-grey); margin-top: 2px; }
  .contact-list { list-style: none; margin-top: 9px; font-family: "Roboto", Arial, sans-serif; font-size: 14px; color: var(--body-ink); }
  .contact-list li { display: flex; align-items: center; gap: 9px; height: 19px; white-space: nowrap; }
  .contact-list svg { width: 13px; height: 13px; fill: var(--ink-blue); flex: none; }

  .front-slogan { position: absolute; left: 0; right: 0; top: 249px; text-align: center; font-family: "Roboto Condensed", Arial, sans-serif; font-size: 14.9px; line-height: 18.5px; color: var(--body-ink); }

  .back-name {
    position: absolute; left: 0; right: 0; top: 86px;
    display: flex; justify-content: center; align-items: center; gap: 10px;
    font-family: "Roboto", Arial, sans-serif; font-weight: 500; font-size: 26px; color: var(--white);
  }
  .back-name__square { width: 14px; height: 14px; background: var(--white); }

  .back-section { position: absolute; left: 20px; right: 20px; }
  .back-section--who { top: 169px; }
  .back-section--what { top: 254px; }
  .back-section__heading { font-weight: 700; font-size: 15px; line-height: 20px; }
  .back-section__body { font-size: 15.2px; line-height: 18px; }
</style>
</head>
<body>
  <section class="card card--front">
    <div class="front-photo" role="img" aria-label="Faded photo of a suburban two-storey house with a green lawn and path"></div>

    <div class="brand-name">
      <span class="brand-name__square"></span>
      <span>KRV Home Solutions LLC</span>
    </div>

    <div class="front-divider"></div>

    <div class="contact-block">
      <h1 class="contact-block__name">JORDAN AVERY</h1>
      <p class="contact-block__title">Principal-Acquisitions</p>
      <ul class="contact-list">
        <li><svg viewBox="0 0 24 24"><path d="M6.6 10.8a15.1 15.1 0 0 0 6.6 6.6l2.2-2.2a1 1 0 0 1 1-.25 11.4 11.4 0 0 0 3.6.57 1 1 0 0 1 1 1V20a1 1 0 0 1-1 1A17 17 0 0 1 3 4a1 1 0 0 1 1-1h3.5a1 1 0 0 1 1 1c0 1.25.2 2.45.57 3.57a1 1 0 0 1-.25 1z"/></svg>555-214-0937</li>
        <li><svg viewBox="0 0 24 24"><path d="M2 5h20v2l-10 7L2 7z"/><path d="M2 9l10 7 10-7v10H2z"/></svg>KRVHOMESOLUTIONS@fernmail.example</li>
        <li><svg viewBox="0 0 24 24"><circle cx="12" cy="12" r="10"/><path d="M12 2v20M2 12h20" stroke="#ffffff" stroke-width="1.5"/></svg>KRVHOMESOLUTIONS.example</li>
      </ul>
    </div>

    <p class="front-slogan">
      Pay all cash. Buy in as is condition.&#8226; No fees,Commisions or closing costs.<br>
      Close quick. No hassles with solutions to meet your unique situation.<br>
      Call today for an offer within 24 hours.
    </p>
  </section>

  <section class="card card--back">
    <div class="back-name">
      <span class="back-name__square"></span>
      <span>KRV Home Solutions LLC</span>
    </div>

    <div class="back-section back-section--who">
      <h2 class="back-section__heading">WHO WE ARE</h2>
      <p class="back-section__body">
        We are a Faith based Real Estate Investment Company. We pay cash for<br>
        homes in any condition and can close quick. Whatever the reason you need<br>
        to sell fast, we can help. We believe in creating win-win solutions to help
      </p>
    </div>

    <div class="back-section back-section--what">
      <h2 class="back-section__heading">WHAT WE DO</h2>
      <p class="back-section__body">
        Buy houses, land, or commercial property as is.<br>
        We find solutions to make the process of selling simple and fair.
      </p>
    </div>
  </section>
</body>
</html>
```